A weight loss and fitness website design

I am into different types of modern weight loss techniques for people who are a little fatty and wish to be physically and mentally fit. Basically, the website is to teach people how to reduce weight using different methods such as diet, exercises, yoga and other forms. I would need an eye catching website which would make visitors want to come back. The will be also be different forms of exercises for a health and fit life. This said, my website is to have two categories of
1) weight loss techniques
2) exercise of fit and healthy living.
I prefer bright colors such as green, blue, yellow, and orange. Imagery should include before and after pictures of people suffering from obesity, people under going exercises.
Designers can get ideas and inspiration from the website fitlumen.com which i was previously part of the team.
Target Market(s)
My target audience are people suffering from obesity, malnutrition and physical deficiency.
Industry/Entity Type
Fitness
Coding
Coded - Design and coding required
Number of Pages Required
1 page
Look and feel

```html
<!DOCTYPE html>
<html lang="en">
<head>
<meta charset="utf-8">
<title>Vantra Fitness</title>
<link rel="stylesheet" href="https://fonts.googleapis.com/css2?family=Montserrat:wght@400;600;700&family=Open+Sans:wght@400;600&display=swap">
<style>
:root{
  --green:#8cc63f;
  --green-dark:#6fae23;
  --blue:#29a9e1;
  --blue-dark:#1a8cc6;
  --ink:#333333;
  --muted:#777777;
  --light:#f2f2f2;
  --white:#ffffff;
  --charcoal:#3a3a3a;
}
*{box-sizing:border-box;margin:0;padding:0}
html,body{width:1200px;height:2400px;overflow:hidden}
body{font-family:"Open Sans",Arial,sans-serif;color:var(--ink);background:var(--white);position:relative}
h1,h2,h3,.nav,.logo,.btn{font-family:"Montserrat",Arial,sans-serif}

.site-header{height:132px;display:flex;align-items:center;justify-content:space-between;padding:0 130px}
.logo{font-weight:700;font-size:30px;color:var(--green);letter-spacing:.5px}
.nav{display:flex;gap:4px;font-size:13px;font-weight:600}
.nav a{color:var(--ink);text-decoration:none;padding:14px 18px}
.nav a.active{background:var(--blue);color:var(--white)}

.hero{position:relative;height:460px;background:linear-gradient(180deg,#ececec 0%,#d9d9d9 100%);overflow:hidden}
.hero-photo{position:absolute;right:170px;top:0;width:420px;height:460px;background:radial-gradient(ellipse at 50% 45%,#e7c4ad 0%,#d9a894 35%,#e28aa0 55%,rgba(220,220,220,0) 78%)}
.hero-copy{position:absolute;left:130px;top:128px}
.hero-copy h1{font-size:32px;font-weight:700;color:var(--ink);letter-spacing:.5px}
.hero-copy p{font-size:14px;color:var(--muted);margin-top:10px}
.btn{display:inline-block;font-size:13px;font-weight:700;color:var(--white);background:var(--blue);padding:12px 20px;border-radius:3px}
.hero-copy .btn{margin-top:38px}
.dots{position:absolute;left:130px;top:446px;display:flex;gap:10px}
.dots span{width:11px;height:11px;border-radius:50%;background:#999}
.dots span:first-child{background:var(--blue)}

.categories{display:flex;height:228px}
.category{flex:1;position:relative;padding:52px 40px 0 132px;color:var(--white)}
.category.weight{background:linear-gradient(90deg,#1c9ad6 0%,#4dbbea 60%,#2aa4de 100%)}
.category.exercise{background:linear-gradient(90deg,#8cc63f 0%,#a6d64f 60%,#7cbc33 100%);padding-left:12px}
.category h3{font-size:17px;font-weight:700;letter-spacing:.3px}
.category p{font-size:12px;line-height:1.6;margin-top:14px;max-width:380px;opacity:.95}
.category .more{display:inline-block;margin-top:22px;font-family:"Montserrat",Arial,sans-serif;font-size:11px;font-weight:700;padding:9px 14px;background:rgba(0,0,0,.18);border-radius:2px}

.welcome{height:508px;text-align:center;padding-top:52px}
.section-title{font-size:30px;font-weight:600;color:var(--ink);letter-spacing:.5px}
.welcome .intro{width:940px;margin:24px auto 0;font-size:12px;line-height:1.7;color:var(--muted)}
.features{display:flex;justify-content:space-between;width:940px;margin:40px auto 0}
.feature{width:260px}
.feature svg{width:90px;height:90px}
.feature h3{font-size:18px;font-weight:600;margin-top:16px}
.feature p{font-size:12px;line-height:1.7;color:var(--muted);margin-top:12px}

.testimonials{position:relative;height:270px;background:var(--light);text-align:center;overflow:hidden}
.testimonial-photo{position:absolute;left:520px;top:0;width:260px;height:270px;background:radial-gradient(ellipse at 50% 40%,rgba(215,180,160,.55) 0%,rgba(200,200,200,.35) 50%,rgba(242,242,242,0) 80%)}
.testimonials .inner{position:relative;padding-top:78px}
.testimonials blockquote{width:900px;margin:22px auto 0;font-size:12px;line-height:1.7;color:var(--muted)}
.testimonials cite{display:block;font-style:normal;font-size:12px;margin-top:10px;color:var(--ink)}
.pager{display:flex;justify-content:center;gap:8px;margin-top:16px}
.pager span{width:22px;height:22px;border:1px solid #999;background:var(--white);display:flex;align-items:center;justify-content:center}

.gallery{height:554px;position:relative;text-align:center;padding-top:20px}
.gallery .section-title{font-size:28px}
.gallery-row{position:absolute;top:132px;left:132px;right:140px;display:flex;justify-content:space-between}
.gallery-item{position:relative;width:452px;height:316px}
.gallery-item.one{background:linear-gradient(90deg,#f1d6cf 0%,#e7a3b7 30%,#f4ece8 50%,#e58aa8 75%,#efdcd6 100%)}
.gallery-item.two{background:linear-gradient(90deg,#dcdcdc 0%,#c79a78 30%,#e9e9e9 50%,#b98b6c 75%,#d6d6d6 100%)}
.tag{position:absolute;bottom:18px;font-size:11px;font-weight:600;color:var(--white);padding:4px 12px}
.tag.before{left:12px;background:var(--blue)}
.tag.after{left:248px;background:var(--green)}
.gallery-arrow{position:absolute;top:262px;width:20px;height:30px}
.gallery-arrow.prev{left:68px}
.gallery-arrow.next{right:78px}

.newsletter{height:116px;background:linear-gradient(180deg,var(--green) 0%,var(--green-dark) 100%);display:flex;align-items:center;justify-content:space-between;padding:0 130px;color:var(--white)}
.newsletter h3{font-size:20px;font-weight:600}
.newsletter p{font-size:11px;margin-top:6px}
.subscribe{display:flex;gap:18px;align-items:center}
.subscribe .field{width:260px;height:34px;background:var(--white);color:#999;font-size:12px;display:flex;align-items:center;padding-left:38px;border-radius:2px;position:relative}
.subscribe .field svg{position:absolute;left:12px;top:10px}
.subscribe .btn{background:var(--charcoal);font-size:11px;padding:10px 18px}

.site-footer{height:140px;background:var(--blue);color:var(--white);text-align:center;padding-top:28px}
.footer-nav{display:flex;justify-content:center;gap:34px;font-family:"Montserrat",Arial,sans-serif;font-size:11px;font-weight:600}
.social{display:flex;justify-content:center;gap:14px;margin-top:16px}
.social span{width:22px;height:22px;border-radius:50%;background:rgba(255,255,255,.85)}
.copyright{font-size:11px;margin-top:14px}
</style>
</head>
<body>

<header class="site-header">
  <div class="logo">VANTRA FITNESS</div>
  <nav class="nav">
    <a class="active">HOME</a><a>ABOUT US</a><a>OUR TRAINING</a><a>OUR COACHES</a><a>BLOG</a><a>CONTACT US</a>
  </nav>
</header>

<section class="hero">
  <div class="hero-photo" role="img" aria-label="Smiling fit woman in a pink sports top measuring her waist with a tape"></div>
  <div class="hero-copy">
    <h1>MODERN WEIGHT LOSS</h1>
    <p>Your own personal trainer, nutritionist and coach free</p>
    <span class="btn">VIEW DETAILS</span>
  </div>
  <div class="dots"><span></span><span></span><span></span></div>
</section>

<section class="categories">
  <article class="category weight" role="img" aria-label="Blue tinted photo of a woman stretching behind the text">
    <h3>WEIGHT LOSS TECHNIQUES</h3>
    <p>Simple proven methods to burn fat safely, eat better every day and keep the weight off for good.</p>
    <span class="more">READ MORE</span>
  </article>
  <article class="category exercise" role="img" aria-label="Green tinted photo of people exercising behind the text">
    <h3>EXERCISE OF FIT AND HEALTHY LIVING</h3>
    <p>Daily workouts and active habits that build strength, boost energy and support a healthy body and mind.</p>
    <span class="more">READ MORE</span>
  </article>
</section>

<section class="welcome">
  <h2 class="section-title">WELCOME VANTRA FITNESS</h2>
  <p class="intro">We help people of every size take the first step toward a lighter, stronger life. Our coaches combine balanced nutrition, smart training and mindful yoga into plans that fit your routine, so progress feels natural and lasts well beyond the first month.</p>
  <div class="features">
    <div class="feature">
      <svg viewBox="0 0 90 90" fill="none" stroke="#333" stroke-width="3" stroke-linejoin="round" stroke-linecap="round">
        <rect x="20" y="14" width="46" height="62" rx="4"/>
        <rect x="33" y="8" width="20" height="10" rx="2"/>
        <line x1="28" y1="30" x2="46" y2="30"/><line x1="28" y1="40" x2="42" y2="40"/>
        <circle cx="56" cy="60" r="14" fill="#fff"/>
        <line x1="56" y1="46" x2="58" y2="40"/>
      </svg>
      <h3>DIET</h3>
      <p>Easy meal plans built around real food, portion control and steady energy through the day.</p>
    </div>
    <div class="feature">
      <svg viewBox="0 0 90 90" fill="#333" stroke="#333" stroke-width="5" stroke-linecap="round">
        <circle cx="45" cy="16" r="8" stroke="none"/>
        <line x1="45" y1="28" x2="45" y2="56"/>
        <line x1="45" y1="32" x2="22" y2="22"/><line x1="45" y1="32" x2="68" y2="22"/>
        <line x1="45" y1="56" x2="34" y2="80"/><line x1="45" y1="56" x2="56" y2="80"/>
        <rect x="10" y="14" width="8" height="16" stroke="none"/><rect x="72" y="14" width="8" height="16" stroke="none"/>
      </svg>
      <h3>EXERCISES</h3>
      <p>Guided routines for every level that raise your heart rate and tone the whole body.</p>
    </div>
    <div class="feature">
      <svg viewBox="0 0 90 90" fill="#333" stroke="#333" stroke-width="4" stroke-linecap="round" stroke-linejoin="round">
        <circle cx="45" cy="22" r="7" stroke="none"/>
        <line x1="45" y1="32" x2="45" y2="58"/>
        <polyline points="45,4 45,10" />
        <polyline points="36,44 45,36 54,44" fill="none"/>
        <line x1="45" y1="58" x2="45" y2="84"/>
        <polyline points="45,62 34,58 45,70" fill="none"/>
      </svg>
      <h3>YOGA</h3>
      <p>Gentle flows that improve balance, ease stress and help you reconnect with your body.</p>
    </div>
  </div>
</section>

<section class="testimonials">
  <div class="testimonial-photo" role="img" aria-label="Faded photo of a happy slim woman raising her arms"></div>
  <div class="inner">
    <h2 class="section-title">TESTIMONIALS</h2>
    <blockquote>Joining this program changed how I think about food and movement. In six months I lost twenty kilos, sleep better and finally enjoy working out. The coaches kept me motivated every single week.</blockquote>
    <cite>Maya Dune</cite>
    <div class="pager">
      <span><svg width="8" height="10" viewBox="0 0 8 10"><polyline points="6,1 2,5 6,9" fill="none" stroke="#555" stroke-width="1.5"/></svg></span>
      <span><svg width="8" height="10" viewBox="0 0 8 10"><polyline points="2,1 6,5 2,9" fill="none" stroke="#555" stroke-width="1.5"/></svg></span>
    </div>
  </div>
</section>

<section class="gallery">
  <h2 class="section-title">OUR GALLERY</h2>
  <svg class="gallery-arrow prev" viewBox="0 0 20 30"><polyline points="15,4 5,15 15,26" fill="none" stroke="#555" stroke-width="3"/></svg>
  <div class="gallery-row">
    <div class="gallery-item one" role="img" aria-label="Before and after photos of a woman in a pink top after weight loss">
      <span class="tag before">Before</span><span class="tag after">After</span>
    </div>
    <div class="gallery-item two" role="img" aria-label="Before and after photos of a man's torso after weight loss">
      <span class="tag before">Before</span><span class="tag after">After</span>
    </div>
  </div>
  <svg class="gallery-arrow next" viewBox="0 0 20 30"><polyline points="5,4 15,15 5,26" fill="none" stroke="#555" stroke-width="3"/></svg>
</section>

<section class="newsletter">
  <div>
    <h3>NEWSLETTER</h3>
    <p>Sign up for weekly tips, workouts and healthy recipes delivered to your inbox.</p>
  </div>
  <div class="subscribe">
    <div class="field">
      <svg width="16" height="12" viewBox="0 0 16 12"><rect x="1" y="1" width="14" height="10" fill="none" stroke="#999"/><polyline points="1,1 8,7 15,1" fill="none" stroke="#999"/></svg>
      Enter your email
    </div>
    <span class="btn">SUBSCRIBE</span>
  </div>
</section>

<footer class="site-footer">
  <nav class="footer-nav"><span>HOME</span><span>ABOUT US</span><span>OUR TRAINING</span><span>OUR COACHES</span><span>BLOG</span><span>CONTACT US</span></nav>
  <div class="social"><span></span><span></span><span></span><span></span></div>
  <p class="copyright">© 2024 Vantra Fitness. All rights reserved.</p>
</footer>

</body>
</html>
```